PowerPoint Design Project

Hi,

Using our logo, we would like a designer to provide us with a powerpoint template that has a unique brand.

To us this means creating a color palette, treatment, a font that plays off of our logo. The color palette needs to blend well with our existing colors, but give us some options, make things "POP".

The color palette needs to include the colors (with RGB numbers), gradients, different graphic styles (solid, transparent, gradient, image fills) and lines (a callout leader line, a multi-color bar to divide content)

The palette and treatment must extend itself to graphs, charts and images.

We would also like to see different parts of our logo applied to the different template slides. For example, on a title slide we would like the image with our logo and tagline. With the end slide we would like to see our logo and URL. We also attached our logo without the tagline and also just the colored cube. So please be creative on how these are incorporated into the deck.

Images are attached.

Thank you
Calvin

Reason: We are extending the deadline 1 day.

Target Market(s)

Large Corporations

Requirements
Must have
• color palette, treatments and consistent fonts. color palette must complement our logo. color palette must extend to graphs, charts and images.

different logo's incorprated into the deck. For example, on a title slide we would like the image with our logo and tagline. With the end slide we would like to see our logo and URL. We also attached our logo without the tagline and also just the colored cube. So please be creative on how these are incorporated into the deck.
Should not have
• We do not want to see designers taking the logo and incorporating them into the background and calling it a template.

```html
<!DOCTYPE html>
<html lang="en">
<head>
<meta charset="utf-8">
<title>Veltacore – Presentation Template</title>
<link rel="stylesheet" href="https://fonts.googleapis.com/css2?family=Alegreya+Sans:wght@300;400;500;700;800&display=swap">
<style>
  :root {
    --page: #ffffff;
    --slide-light-top: #fbfbfd;
    --slide-light-bottom: #e3e5ec;
    --ink: #231f20;
    --ink-soft: #3a3a3a;
    --brand-blue: #1f5fae;
    --brand-green: #8cc63f;
    --brand-teal: #3cb4c8;
    --muted: #c9ccd6;
    --orange-top: #f8bf33;
    --orange-bottom: #d86a27;
    --orange-word: #fbc93a;
    --footer-top: #4a4e59;
    --footer-bottom: #2b2e35;
    --suit-top: #d9dce3;
    --suit-bottom: #1d2433;
  }
  * { box-sizing: border-box; margin: 0; padding: 0; }
  html, body { width: 1200px; height: 905px; overflow: hidden; background: var(--page); }
  body { position: relative; font-family: "Alegreya Sans", Arial, sans-serif; color: var(--ink); }

  .slide { position: absolute; overflow: hidden; width: 581px; height: 436px; }
  .slide--light { background: linear-gradient(180deg, var(--slide-light-top), var(--slide-light-bottom)); }
  .slide--title { left: 14px; top: 10px; }
  .slide--section { left: 605px; top: 10px; background: linear-gradient(180deg, var(--orange-top), var(--orange-bottom)); }
  .slide--content { left: 14px; top: 457px; background: linear-gradient(180deg, #ffffff, #eef0f4); }
  .slide--end { left: 605px; top: 458px; }

  .brand { position: absolute; display: flex; align-items: center; gap: 14px; }
  .brand__mark { width: 62px; height: 62px; background: var(--brand-blue); flex: none; }
  .brand__name { font-weight: 800; font-size: 52px; line-height: 1; color: var(--ink); letter-spacing: -0.5px; }
  .brand__line { font-size: 17px; color: var(--brand-blue); margin-top: 2px; letter-spacing: 0.2px; }
  .slide--title .brand { left: 96px; top: 178px; }
  .slide--end .brand { left: 96px; top: 178px; }

  .section-word { position: absolute; left: 94px; top: 176px; display: flex; align-items: center; gap: 16px; }
  .section-word__mark { width: 62px; height: 62px; background: var(--orange-word); opacity: .9; }
  .section-word__text { font-weight: 700; font-size: 66px; color: var(--orange-word); line-height: 1; }

  .content__rule-top { position: absolute; left: 0; top: 0; width: 100%; height: 5px; background: var(--brand-teal); }
  .content__heading { position: absolute; left: 8px; top: 10px; font-weight: 400; font-size: 22px; color: var(--brand-teal); }
  .content__underline { position: absolute; left: 0; top: 38px; width: 280px; height: 2px; background: var(--muted); }
  .content__tag { position: absolute; left: 290px; top: 28px; display: flex; align-items: center; gap: 7px; }
  .content__tag-mark { width: 18px; height: 18px; background: var(--muted); }
  .content__tag-name { font-weight: 700; font-size: 19px; color: var(--muted); }

  .content__photo { position: absolute; left: 32px; top: 56px; width: 200px; height: 337px; background: linear-gradient(180deg, var(--suit-top) 0%, #8d97a8 28%, var(--suit-bottom) 42%, var(--suit-bottom) 100%); border-radius: 90px 90px 0 0; }

  .points { position: absolute; left: 258px; top: 72px; width: 310px; }
  .points__title { font-weight: 700; font-size: 13px; color: var(--brand-teal); margin: 0 0 8px 26px; }
  .points__item { position: relative; padding-left: 25px; font-size: 9.4px; line-height: 12.4px; color: var(--ink-soft); margin-bottom: 13px; }
  .points__item::before { content: ""; position: absolute; left: 1px; top: 2px; width: 9px; height: 9px; background: var(--brand-blue); }
  .points__divider { height: 1px; background: #d9dbe2; margin: 14px 0 14px 16px; }

  .footer { position: absolute; left: 0; bottom: 0; width: 100%; height: 43px; background: linear-gradient(180deg, var(--footer-top), var(--footer-bottom)); color: var(--brand-green); font-size: 10px; }
  .footer__page { position: absolute; left: 14px; top: 15px; }
  .footer__mail { position: absolute; left: 185px; top: 15px; }
  .footer__mark { position: absolute; left: 280px; top: 11px; width: 20px; height: 20px; background: var(--brand-green); }
  .footer__web { position: absolute; left: 315px; top: 15px; }
</style>
</head>
<body>

<section class="slide slide--light slide--title">
  <div class="brand">
    <span class="brand__mark"></span>
    <div>
      <div class="brand__name">veltacore</div>
      <div class="brand__line">analyze . elevate . transform</div>
    </div>
  </div>
</section>

<section class="slide slide--section">
  <div class="section-word">
    <span class="section-word__mark"></span>
    <span class="section-word__text">transform</span>
  </div>
</section>

<section class="slide slide--content">
  <div class="content__rule-top"></div>
  <h2 class="content__heading">analyze</h2>
  <div class="content__underline"></div>
  <div class="content__tag">
    <span class="content__tag-mark"></span>
    <span class="content__tag-name">veltacore</span>
  </div>

  <div class="content__photo" role="img" aria-label="Photo of a business professional in a dark suit standing with hands clasped"></div>

  <div class="points">
    <h3 class="points__title">Analyze</h3>
    <p class="points__item">Aenean ridiculus <b>tortor</b> quis interdum id habitant ad, natoque consectetuer nisl auctor libero quisque euismod ante inceptos malesuada ligula mattis.</p>
    <p class="points__item"><b>Nulla,</b> netus pulvinar pellentesque porttitor purus maecenas tellus hac nulla lacus. Lorem. Nostra laoreet nulla, dis cursus nascetur dolor odio Eu Magna molestie montes dui mus cursus habitasse mauris tempor.</p>
    <p class="points__item">Varius inceptos nascetur mollis dui aptent ultrices. Pretium pulvinar ante lobortis convallis lectus netus vitae penatibus eros at blandit. Parturient.</p>
    <div class="points__divider"></div>
    <h3 class="points__title" style="margin-left:8px">Elevate</h3>
    <p class="points__item">Aenean ridiculus <b>tortor</b> quis interdum id habitant ad, natoque consectetuer nisl auctor libero quisque euismod ante inceptos malesuada ligula mattis.</p>
    <p class="points__item"><b>Nulla,</b> netus pulvinar pellentesque porttitor purus maecenas tellus hac nulla lacus. Lorem. Nostra laoreet nulla, dis cursus nascetur dolor odio</p>
  </div>

  <footer class="footer">
    <span class="footer__page">3</span>
    <span class="footer__mail">info@veltacore.com</span>
    <span class="footer__mark"></span>
    <span class="footer__web">www.veltacore.com</span>
  </footer>
</section>

<section class="slide slide--light slide--end">
  <div class="brand">
    <span class="brand__mark"></span>
    <div>
      <div class="brand__name">veltacore</div>
      <div class="brand__line">www.veltacore.com</div>
    </div>
  </div>
</section>

</body>
</html>
```